Buch-/E-Book-Cover für einen historischen Roman
Zielgruppe
Buchautor historische Romane, Zielgruppe 60 % weiblich, 35 +
Aufgabenstellung
Die Farbgebung und Schrifttype sollen sich an die ersten 4 Bänder der Serie 'Das Findelkind und der Abt' https://www.buchkontor.de/Findelkind-Abt-Historischer-Roman-ebook/dp/Q417K2RMWX, anpassen, da der Buchtitel 'Die Gräfin und der Falschspieler' der 5 Band dieser Serie ist. Die Grafik kann aber etwas abweichen, im Mittelpunkt des Romans steht das Verschwinden eines Siegelrings. Der sollte abgebildet sein, in dem Roman werden Frau und kleiner Sohn des Herzogs entführt und in einem alten Herrenhaus im englischen Marschland wiedergefunden.

```html
<!DOCTYPE html>
<html lang="de">
<head>
<meta charset="utf-8">
<title>Die Gräfin und der Falschspieler – Buch fünf</title>
<link rel="stylesheet" href="https://fonts.googleapis.com/css2?family=Cinzel:wght@400;500&family=EB+Garamond:wght@500;600&family=IM+Fell+English:ital@1&display=swap">
<style>
  :root {
    --parchment-light: #f1e0b4;
    --parchment-mid: #e4c98e;
    --parchment-dark: #c89f5c;
    --stain: rgba(190, 140, 60, 0.28);
    --stain-dark: rgba(150, 95, 35, 0.22);
    --author-red: #7a1712;
    --ink: #0b0806;
    --ring-gold: #d98a35;
    --ring-deep: #a2521b;
    --hill: #a08662;
    --water: #d8c49c;
    --ground: #6b5236;
    --ground-dark: #3f3020;
  }
  html, body {
    margin: 0;
    padding: 0;
    width: 850px;
    height: 1200px;
    overflow: hidden;
    background: #ffffff;
  }
  .cover {
    position: relative;
    width: 850px;
    height: 1200px;
    overflow: hidden;
    background:
      radial-gradient(circle at 12% 8%, var(--stain-dark) 0, transparent 90px),
      radial-gradient(circle at 88% 6%, var(--stain-dark) 0, transparent 110px),
      radial-gradient(circle at 25% 30%, var(--stain) 0, transparent 70px),
      radial-gradient(circle at 78% 45%, var(--stain) 0, transparent 80px),
      radial-gradient(circle at 18% 58%, var(--stain) 0, transparent 90px),
      radial-gradient(circle at 90% 70%, var(--stain-dark) 0, transparent 40px),
      radial-gradient(circle at 40% 75%, var(--stain) 0, transparent 100px),
      radial-gradient(circle at 5% 40%, var(--stain-dark) 0, transparent 60px),
      radial-gradient(ellipse at 50% 45%, var(--parchment-light) 0%, var(--parchment-mid) 60%, var(--parchment-dark) 100%);
  }
  .fold {
    position: absolute;
    left: 0;
    top: 364px;
    width: 100%;
    height: 1px;
    background: rgba(120, 85, 40, 0.18);
  }
  .author {
    position: absolute;
    top: 118px;
    left: 0;
    width: 100%;
    margin: 0;
    text-align: center;
    font-family: "Cinzel", serif;
    font-weight: 400;
    font-size: 68px;
    letter-spacing: 1px;
    color: var(--author-red);
  }
  .signet-ring {
    position: absolute;
    left: 385px;
    top: 248px;
    width: 78px;
    height: 82px;
    border-radius: 46% 50% 50% 46%;
    background: radial-gradient(circle at 38% 32%, #f3b96a 0%, var(--ring-gold) 45%, var(--ring-deep) 100%);
    box-shadow: 0 14px 20px rgba(90, 55, 20, 0.3);
  }
  .title {
    position: absolute;
    top: 373px;
    left: 0;
    width: 100%;
    margin: 0;
    text-align: center;
    color: var(--ink);
    font-weight: 600;
  }
  .title-line {
    display: block;
    font-family: "EB Garamond", serif;
    font-weight: 600;
    font-size: 88px;
    line-height: 92px;
    letter-spacing: 1px;
  }
  .title-line--long {
    margin-top: 9px;
    font-size: 78px;
  }
  .title-join {
    display: block;
    font-family: "IM Fell English", serif;
    font-style: italic;
    font-weight: 400;
    font-size: 44px;
    line-height: 56px;
  }
  .flourish {
    position: absolute;
    left: 373px;
    top: 642px;
    width: 104px;
    height: 38px;
    border-radius: 19px;
    background: rgba(50, 35, 20, 0.16);
  }
  .volume {
    position: absolute;
    top: 710px;
    left: 0;
    width: 100%;
    margin: 0;
    text-align: center;
    font-family: "EB Garamond", serif;
    font-weight: 500;
    font-size: 33px;
    letter-spacing: 1px;
    color: var(--ink);
  }
  .landscape {
    position: absolute;
    left: 0;
    bottom: 0;
    width: 850px;
    height: 330px;
    background:
      linear-gradient(to right, rgba(0,0,0,0) 0%, rgba(0,0,0,0) 48%, rgba(60,45,30,0.55) 50%, rgba(60,45,30,0.55) 84%, rgba(0,0,0,0) 86%) 0 60px / 100% 190px no-repeat,
      linear-gradient(to bottom, rgba(160,134,98,0) 0%, rgba(160,134,98,0.35) 40%, var(--water) 55%, var(--ground) 68%, var(--ground-dark) 100%);
  }
</style>
</head>
<body>
  <main class="cover">
    <div class="fold"></div>
    <p class="author">JONAS WERBECK</p>
    <div class="signet-ring" role="img" aria-label="Goldener Siegelring mit Lilienwappen"></div>
    <h1 class="title">
      <span class="title-line">DIE GRÄFIN</span>
      <span class="title-join">und der</span>
      <span class="title-line title-line--long">FALSCHSPIELER</span>
    </h1>
    <div class="flourish" role="img" aria-label="Geschwungenes Zierornament"></div>
    <p class="volume">BUCH FÜNF</p>
    <div class="landscape" role="img" aria-label="Altes Herrenhaus am Seeufer in hügeliger Landschaft mit einem Reiter im Gegenlicht"></div>
  </main>
</body>
</html>
```